Maplecrest Disability - Social Security Disability Attorneys

Our company is expanding to attract clients nationwide for our social security disability practice. We have a logo, but I am looking for a creative and elegant letterhead that projects an image of being technologically advanced but still professional enough for the legal field. I am looking for the "wow factor" combined with this is still professional enough for a law practice.

Requesting letterhead and business card design
Updates

Had to update and change the logo. The previous logo had a typo. Please send updates with the new logo for consideration. The letterhead and business cards should be professional enough to be used for a law firm. Thanks.

Industry/Entity Type

Law Practice, Law Firm, Healthcare Industry, Government

Colors

Designer to choose colors to be used in the design.

Requirements
Nice to have
• **Please create a vertical design for the business card**

```html
<!DOCTYPE html>
<html lang="en">
<head>
<meta charset="utf-8">
<title>Maplecrest Disability – Business Card</title>
<link rel="stylesheet" href="https://fonts.googleapis.com/css2?family=Figtree:wght@400;500;700;800&display=swap">
<style>
  :root {
    --stage: #209dd9;
    --card-dark: #1b1b1d;
    --card-mid: #232324;
    --facet: #29292a;
    --brand-blue: #4b62b2;
    --accent-orange: #f0892a;
    --text-light: #ffffff;
  }
  * { box-sizing: border-box; margin: 0; padding: 0; }
  html, body { width: 1200px; height: 1128px; overflow: hidden; }
  body {
    background: var(--stage);
    font-family: "Figtree", Arial, sans-serif;
    color: var(--text-light);
    position: relative;
  }
  .card {
    position: absolute;
    top: 129px;
    height: 870px;
    border-radius: 38px;
    background: var(--card-dark);
    overflow: hidden;
    box-shadow: 0 14px 36px rgba(0, 20, 50, 0.55);
  }
  .card--front { left: 69px; width: 501px; }
  .card--back { left: 632px; width: 497px; }
  .card__facets { position: absolute; inset: 0; width: 100%; height: 100%; }
  .block { position: absolute; left: 0; right: 0; text-align: center; }

  .brand__mark {
    position: absolute;
    left: 50%;
    width: 22px; height: 22px;
    margin-left: -11px;
    border-radius: 50%;
    background: var(--accent-orange);
  }
  .brand__name {
    font-weight: 500;
    color: var(--brand-blue);
    letter-spacing: 2px;
    white-space: nowrap;
    line-height: 1;
  }
  .brand__tagline {
    font-weight: 500;
    color: var(--brand-blue);
    letter-spacing: 2.4px;
    white-space: nowrap;
    line-height: 1;
  }
  .card--front .brand__mark { top: 258px; }
  .card--front .brand__name { top: 301px; font-size: 27px; }
  .card--front .brand__tagline { top: 332px; font-size: 8.5px; }
  .card--back .brand__mark { top: 116px; }
  .card--back .brand__name { top: 155px; font-size: 31px; }
  .card--back .brand__tagline { top: 190px; font-size: 9.5px; }

  .scan-note { top: 570px; font-size: 16px; font-weight: 500; }
  .practice-areas { top: 702px; font-size: 20px; font-weight: 500; line-height: 31px; }

  .person__name { top: 374px; font-size: 31px; font-weight: 800; letter-spacing: 0.3px; }
  .person__role {
    top: 412px;
    font-size: 21px;
    display: flex; align-items: center; justify-content: center; gap: 5px;
  }
  .person__role::before, .person__role::after {
    content: ""; width: 64px; height: 1.5px; background: var(--text-light);
  }
  .address { top: 543px; font-size: 20px; line-height: 29px; }
  .contact-icons {
    top: 637px;
    display: flex; justify-content: center; gap: 34px;
  }
  .contact-icons svg { width: 21px; height: 21px; fill: var(--accent-orange); }
  .contact-list { top: 680px; font-size: 20px; line-height: 32.5px; }
</style>
</head>
<body>

<section class="card card--front">
  <svg class="card__facets" viewBox="0 0 501 870" preserveAspectRatio="none" aria-hidden="true">
    <polygon points="0,432 501,432 501,870 0,870" fill="var(--card-mid)"/>
    <polygon points="501,146 501,870 280,870 330,560" fill="var(--facet)" opacity="0.6"/>
    <polygon points="0,560 260,640 0,730" fill="#1e1e20"/>
    <polygon points="0,870 200,780 501,780 501,870" fill="#1f1f20" opacity="0.7"/>
  </svg>
  <span class="brand__mark"></span>
  <p class="block brand__name">MAPLECREST DISABILITY</p>
  <p class="block brand__tagline">SOCIAL SECURITY DISABILITY ATTORNEYS</p>
  <p class="block scan-note">Scan Me To Visit Our Site</p>
  <p class="block practice-areas">Law Practice, Law Firm,<br>Healthcare Industry, Government</p>
</section>

<section class="card card--back">
  <svg class="card__facets" viewBox="0 0 497 870" preserveAspectRatio="none" aria-hidden="true">
    <polygon points="0,432 497,432 497,870 0,870" fill="var(--card-mid)"/>
    <polygon points="497,146 497,870 180,870 330,320" fill="var(--facet)" opacity="0.6"/>
    <polygon points="0,560 230,640 0,740" fill="#1e1e20"/>
    <polygon points="497,780 497,870 420,870" fill="#1a1a1b"/>
  </svg>
  <span class="brand__mark"></span>
  <p class="block brand__name">MAPLECREST DISABILITY</p>
  <p class="block brand__tagline">SOCIAL SECURITY DISABILITY ATTORNEYS</p>

  <h1 class="block person__name">DANIEL WHITCOMBE</h1>
  <p class="block person__role">Co-Founder</p>

  <p class="block address">Suite 7, Level 18, Wattle<br>Street Sydney NSW 2000</p>

  <div class="block contact-icons">
    <svg viewBox="0 0 24 24" aria-label="Phone"><path d="M6.6 10.8a15.1 15.1 0 0 0 6.6 6.6l2.2-2.2c.3-.3.7-.4 1-.2 1.1.4 2.3.6 3.6.6.6 0 1 .4 1 1V20c0 .6-.4 1-1 1A17 17 0 0 1 3 4c0-.6.4-1 1-1h3.5c.6 0 1 .4 1 1 0 1.3.2 2.5.6 3.6.1.3 0 .7-.2 1z"/></svg>
    <svg viewBox="0 0 24 24" aria-label="Email"><path d="M2 5h20v14H2z" /><path d="M2 5l10 8 10-8" fill="none" stroke="#232324" stroke-width="1.6"/></svg>
    <svg viewBox="0 0 24 24" aria-label="Website"><circle cx="12" cy="12" r="10"/><path d="M2 12h20M12 2c3 3 3 17 0 20M12 2c-3 3-3 17 0 20" fill="none" stroke="#232324" stroke-width="1.4"/></svg>
  </div>

  <p class="block contact-list">555-214-7730<br>Info@maplecrestdisability.com<br>www.maplecrestdisability.com</p>
</section>

</body>
</html>
```